Wir suchen ein Design für eine Fotorahmen Verpackung
Zielgruppe
Wir machen Lifestyle Produkte aus Silber Edelstahl und Glas. Wir produzieren Kerzenleuchter, Bilderrahmen, Vasen etc. ausschließlich Luxusgüter.
Zielgruppe: ab 30, wohlhabend
Aufgabenstellung
Wir haben derzeit unsere Bilderrahmen in einem schlichten schwarzen Papp-Verpackung. Für die Zukunft soll unsere Marke mehr zur Geltung kommen. Das Inlay des Rahmen ist sichtbar auf den Bildern, in dem Look and Feel soll auch ungefähr die Verpackung werden. Farben sind derzeit nicht vorgegeben, aber ein weisser oder schwarzer Hintergrund ist wohl sinnvoll. Der Druck der Verpackung soll in Asien erfolgen, also direkt dort wo die Rahmen herkommen.
Die Verpackung wie sie jetzt aussieht ist als Bild dabei. Example 1 und Example 2 gefällt mir sehr gut, in diese Richtung soll es gehen.
Wir sind auch in Zukunft auf der Suche nach weiteren Verpackungs Designs wir haben derzeit 16000 Produkte im Portfolio.
Bitte diese Worte auf die Verpackung:
Bilderrahmen, Picture Frame, Cadre Photo, Marco De Fotos, Cornice Portafoto

```html
<!DOCTYPE html>
<html lang="de">
<head>
<meta charset="utf-8">
<title>Lunvar – Faltschachtel Bilderrahmen</title>
<link rel="stylesheet" href="https://fonts.googleapis.com/css2?family=Cinzel:wght@500&display=swap">
<style>
  :root {
    --paper: #ffffff;
    --print-black: #000000;
    --cut-orange: #e8690b;
    --cut-blue: #1ea0dc;
    --fold-line: #1a1a1a;
    --brand-white: #ffffff;
  }
  html, body {
    margin: 0;
    padding: 0;
    width: 1200px;
    height: 942px;
    overflow: hidden;
    background: var(--paper);
  }
  .dieline-sheet {
    display: block;
    width: 1200px;
    height: 942px;
  }
  .cut-outer { fill: var(--paper); stroke: var(--cut-orange); stroke-width: 18; stroke-linejoin: round; }
  .cut-inner-mask { fill: none; stroke: var(--paper); stroke-width: 18; }
  .cut-inner { fill: none; stroke: var(--cut-blue); stroke-width: 3; }
  .cut-slit { fill: none; stroke: var(--cut-blue); stroke-width: 2; }
  .fold { fill: none; stroke: var(--fold-line); stroke-width: 2; stroke-dasharray: 7 6; }
  .print-panel { fill: var(--print-black); }
  .brand-name {
    font-family: "Cinzel", "Times New Roman", serif;
    font-weight: 500;
    fill: var(--brand-white);
    text-anchor: middle;
    dominant-baseline: middle;
  }
  .brand-name--front { font-size: 150px; }
  .brand-name--flap { font-size: 28px; }
</style>
</head>
<body>
<svg class="dieline-sheet" viewBox="0 0 2180 1712" xmlns="http://www.w3.org/2000/svg">
  <defs>
    <path id="box-outline" d="M160 297 L160 140 Q163 100 200 75 L957 75 Q998 100 1000 140 L1000 297 L1013 185 L1095 185 L1105 193 L1122 258 L1137 272 L1140 285 L1140 297 L1480 297 L1480 265 Q1482 240 1505 240 L1580 240 Q1603 240 1605 265 L1605 297 L1953 297 L1955 280 L1962 265 L1975 255 L1990 190 L2000 185 L2075 185 L2083 192 L2093 292 L2100 298 L2105 310 L2105 1405 L2100 1410 L2100 1435 L2095 1443 L2083 1455 L2070 1510 L2060 1517 L1980 1517 L1970 1510 L1962 1430 L1962 1545 Q1962 1605 1925 1635 L1165 1635 Q1125 1605 1125 1545 L1125 1430 L1110 1510 L1100 1517 L1030 1517 L1018 1510 L1003 1455 L990 1443 L985 1433 L985 1412 L160 1412 L80 1390 L70 1378 L70 325 L80 315 Z"/>
    <clipPath id="inside-box"><use href="#box-outline"/></clipPath>
    <radialGradient id="rosette-tones" cx="50%" cy="50%" r="50%">
      <stop offset="0" stop-color="#000000"/>
      <stop offset="0.12" stop-color="#000000"/>
      <stop offset="0.3" stop-color="#9a9a9a"/>
      <stop offset="0.6" stop-color="#5a5a5a"/>
      <stop offset="1" stop-color="#000000"/>
    </radialGradient>
  </defs>

  <g class="cut-contour">
    <use href="#box-outline" class="cut-outer"/>
    <g clip-path="url(#inside-box)">
      <use href="#box-outline" class="cut-inner-mask"/>
      <use href="#box-outline" class="cut-inner"/>
    </g>
  </g>

  <g class="cut-slits">
    <path class="cut-slit" d="M165 162 H208 V170 M948 170 V162 H990 M522 166 V160 H633 V166"/>
    <path class="cut-slit" d="M992 162 V300"/>
    <path class="cut-slit" d="M1490 300 V358 M1600 300 V358"/>
    <path class="cut-slit" d="M1132 1547 H1175 V1540 M1915 1540 V1547 H1958"/>
  </g>

  <g class="fold-lines">
    <path class="fold" d="M208 165 H522 M633 165 H948"/>
    <path class="fold" d="M165 302 H2093"/>
    <path class="fold" d="M165 302 V1405"/>
    <path class="fold" d="M992 300 V1405"/>
    <path class="fold" d="M1132 300 V1545"/>
    <path class="fold" d="M1958 300 V1545"/>
    <path class="fold" d="M992 1405 H2093"/>
    <path class="fold" d="M1175 1545 H1915"/>
  </g>

  <g class="print-panels">
    <rect class="print-panel panel-top-flap" x="204" y="201" width="749" height="63"/>
    <rect class="print-panel panel-front" x="204" y="341" width="749" height="1023"/>
    <rect class="print-panel panel-side" x="1030" y="341" width="63" height="1023"/>
    <rect class="print-panel panel-back" x="1170" y="341" width="749" height="1026"/>
    <rect class="print-panel panel-side" x="1997" y="341" width="67" height="1023"/>
    <rect class="print-panel panel-bottom-flap" x="1170" y="1445" width="749" height="62"/>
  </g>

  <text class="brand-name brand-name--front" x="590" y="845" textLength="620" lengthAdjust="spacingAndGlyphs">LUNVAR</text>

  <circle class="back-rosette" cx="1545" cy="853" r="345" fill="url(#rosette-tones)" role="img" aria-label="Feine weiße Linienrosette aus überlagerten Blütenblättern auf schwarzem Grund"/>

  <text class="brand-name brand-name--flap" x="1555" y="1476">LUNVAR</text>
</svg>
</body>
</html>
```